Lanternfield Drinks business cards

We need a business card design for our new logo. The company is modern, progressive, professional, yet approachable. The key products are ready to drink bottles and cans of coffee based beverages.
These cards will be a critical part of the first impression made by our sales organization, business development team, and all external facing personnel.
Card can be a vertical or horizontal orientation.

Target Market(s)

Customers, suppliers, business partners

Industry/Entity Type

Business

Contact Information for Business Card

Business cards should feature Company Name and Logo.

Font styles to use
Serif

Colors

Designer to choose colors to be used in the design.

Requirements
Must have
• Strong readability of Name, phone #, mobile number and email address.
• Job title, website url, Street Address, and other details can be secondary level readability.
Nice to have
• High impact, simplistic quality design.
• Ok to utilize the 'H in the box' separate from the company name

```html
<!DOCTYPE html>
<html lang="en">
<head>
<meta charset="utf-8">
<title>Lanternfield Drinks business cards</title>
<link href="https://fonts.googleapis.com/css2?family=Lora:wght@400;600&display=swap" rel="stylesheet">
<style>
  :root {
    --bg: #8e8e8e;
    --orange: #e8572a;
    --orange-light: #f2683a;
    --orange-dark: #d44e22;
    --white: #ffffff;
    --paper: #f7f7f7;
    --ink: #222222;
    --rule: #9a9a9a;
  }
  * { margin: 0; padding: 0; box-sizing: border-box; }
  html, body { width: 1200px; height: 900px; overflow: hidden; }
  body {
    background: var(--bg);
    font-family: "Lora", Georgia, serif;
    position: relative;
  }
  .card {
    position: absolute;
    width: 580px;
    height: 332px;
    border-radius: 18px;
    box-shadow: 0 10px 24px rgba(0,0,0,.28);
    overflow: hidden;
  }
  /* Front side */
  .card--front {
    left: 60px; top: 100px;
    background: linear-gradient(135deg, var(--orange-dark), var(--orange-light));
    color: var(--white);
    display: flex; flex-direction: column; align-items: center; justify-content: center;
  }
  .brand {
    display: flex; align-items: center; gap: 14px;
    font-weight: 600; letter-spacing: .04em; text-transform: uppercase;
    white-space: nowrap;
  }
  .brand__square {
    width: 34px; height: 34px; background: currentColor; flex: none;
  }
  .card--front .brand { flex-direction: column; gap: 18px; font-size: 30px; }
  .card--front .brand__square { width: 64px; height: 64px; }
  .front__rule { width: 300px; height: 2px; background: var(--white); margin-top: 14px; opacity: .9; }
  .front__url { margin-top: 34px; font-size: 15px; letter-spacing: .02em; }

  /* Back side */
  .card--back {
    left: 560px; top: 480px;
    background: linear-gradient(160deg, var(--white), var(--paper));
    color: var(--ink);
  }
  .back__header {
    position: absolute; left: 38px; right: 36px; top: 46px;
    display: flex; align-items: center; gap: 18px;
  }
  .back__header .brand { color: var(--orange); font-size: 24px; flex: none; }
  .back__top-rule { flex: 1; height: 1px; background: var(--rule); }
  .person { position: absolute; left: 38px; top: 150px; }
  .person__name { color: var(--orange); font-size: 30px; font-weight: 600; line-height: 1.1; }
  .person__title { font-size: 20px; margin-top: 2px; }
  .person__rule { width: 260px; height: 1px; background: var(--rule); margin-top: 12px; }
  .contacts { list-style: none; margin-top: 12px; font-size: 16px; }
  .contacts li { display: flex; align-items: center; gap: 10px; margin-bottom: 6px; }
  .contacts svg { width: 15px; height: 15px; fill: var(--orange); flex: none; }
  .address {
    position: absolute; right: 36px; top: 150px;
    text-align: right; font-size: 16px; line-height: 1.45; font-style: normal;
  }
</style>
</head>
<body>

<section class="card card--front" aria-label="Card front">
  <div class="brand">
    <span class="brand__square"></span>
    <span class="brand__name">Lanternfield Drinks</span>
  </div>
  <div class="front__rule"></div>
  <p class="front__url">www.lanternfielddrinks.com</p>
</section>

<section class="card card--back" aria-label="Card back">
  <div class="back__header">
    <div class="brand">
      <span class="brand__square"></span>
      <span class="brand__name">Lanternfield Drinks</span>
    </div>
    <div class="back__top-rule"></div>
  </div>

  <div class="person">
    <h1 class="person__name">Aldo Mercer</h1>
    <p class="person__title">President</p>
    <div class="person__rule"></div>
    <ul class="contacts">
      <li>
        <svg viewBox="0 0 24 24" aria-hidden="true"><path d="M6.6 10.8a15.1 15.1 0 0 0 6.6 6.6l2.2-2.2c.3-.3.7-.4 1-.2 1.1.4 2.3.6 3.6.6.6 0 1 .4 1 1V20c0 .6-.4 1-1 1A17 17 0 0 1 3 4c0-.6.4-1 1-1h3.5c.6 0 1 .4 1 1 0 1.3.2 2.5.6 3.6.1.3 0 .7-.2 1z"/></svg>
        555 014 2273
      </li>
      <li>
        <svg viewBox="0 0 24 24" aria-hidden="true"><path d="M2 5h20v14H2z M2 5l10 8 10-8" /></svg>
        info@lanternfielddrinks.com
      </li>
      <li>
        <svg viewBox="0 0 24 24" aria-hidden="true"><circle cx="12" cy="12" r="10"/><path d="M2 12h20M12 2c3 3 3 17 0 20M12 2c-3 3-3 17 0 20" stroke="#fff" stroke-width="1.4" fill="none"/></svg>
        www.lanternfielddrinks.com
      </li>
    </ul>
  </div>

  <address class="address">
    Level 2, 17 Harlow Lane<br>
    Fernbrook, VIC 3999
  </address>
</section>

</body>
</html>
```